Beacon Advisory Website

I currently have a website www.beaconadvisoryinc.com. We are a IT Consulting Company. Our website will pretty much tell out our services. I am looking to enhance my website and make it look more professional. Looking for very classy and Contemporary look and design for my website.

It Company

```html
<!DOCTYPE html>
<html lang="en">
<head>
<meta charset="utf-8">
<title>Beacon Advisory</title>
<link href="https://fonts.googleapis.com/css2?family=Raleway:wght@400;500;600;700&family=Open+Sans:ital,wght@0,400;0,600;0,700;1,400&display=swap" rel="stylesheet">
<style>
:root{
  --brand:#0a9fd8;
  --brand-dark:#0a6fb0;
  --navy:#1560a6;
  --navy-deep:#0e3f70;
  --ink:#222;
  --muted:#555;
  --light:#e9ecef;
  --white:#fff;
  --topbar:#f1f2f3;
}
*{margin:0;padding:0;box-sizing:border-box}
html,body{width:672px;height:1200px;overflow:hidden}
body{position:relative;font-family:"Open Sans",Arial,sans-serif;color:var(--ink);background:var(--white)}
.abs{position:absolute}
.heading{font-family:"Raleway",Arial,sans-serif}

/* top bar */
.topbar{left:0;top:0;width:672px;height:50px;background:linear-gradient(#fafafa,#eceeef);border-top:2px solid var(--brand)}
.brand{display:flex;align-items:center;gap:6px;font-family:"Raleway",Arial,sans-serif;font-weight:700;color:var(--navy)}
.brand-mark{width:22px;height:22px;background:var(--brand)}
.topbar .brand{left:60px;top:12px;font-size:15px}
.contact-chip{top:13px;display:flex;gap:6px;align-items:center}
.contact-chip .dot{width:19px;height:19px;border-radius:50%;background:var(--navy);display:flex;align-items:center;justify-content:center}
.contact-chip .label{font-size:7px;font-weight:700;color:var(--navy);line-height:10px}
.contact-chip .value{font-size:8.5px;color:#333;line-height:11px}

/* nav */
.nav{left:0;top:50px;width:672px;height:24px;background:linear-gradient(#0a9fd8,#0b7fc2);display:flex;padding-left:60px}
.nav a{font-family:"Raleway",Arial,sans-serif;font-size:7.5px;font-weight:700;color:var(--white);text-decoration:none;height:24px;display:flex;align-items:center;justify-content:center;border-right:1px solid rgba(255,255,255,.15)}
.nav a.active{background:#27b7ec}

/* hero */
.hero{left:0;top:74px;width:672px;height:228px;background:#050607}
.hero-visual{left:380px;top:74px;width:292px;height:228px;background:radial-gradient(circle at 62% 42%,#cfe9fb 0,#4f9ad6 18%,#16436f 45%,#0a1a2b 75%,#050607 100%)}
.hero-title{left:60px;top:144px;width:300px;font-size:13.5px;line-height:18.5px;font-weight:700;color:var(--white);text-transform:uppercase;letter-spacing:.2px}
.btn-more{left:60px;top:213px;width:69px;height:22px;background:var(--brand);color:var(--white);font-size:7px;font-weight:700;display:flex;align-items:center;justify-content:center;clip-path:polygon(0 0,90% 0,100% 30%,100% 100%,0 100%)}

/* welcome */
.welcome{left:0;top:302px;width:672px;height:108px;background:linear-gradient(#0b9bd6,#0a86c8)}
.welcome h1{left:0;top:310px;width:672px;text-align:center;font-size:17.5px;font-weight:400;color:var(--white)}
.welcome-rule{left:200px;top:338px;width:272px;height:1px;background:rgba(255,255,255,.5)}
.welcome p{left:66px;top:351px;width:540px;text-align:center;font-size:7.2px;line-height:12.5px;color:#e4f3fb}
.plus{left:324px;top:395px;width:24px;height:15px;background:#333;color:#fff;font-size:12px;font-weight:700;display:flex;align-items:center;justify-content:center;border-radius:2px 2px 0 0}

/* features */
.feature{top:410px;width:184px;text-align:center}
.feature h3{position:absolute;top:130px;width:100%;font-size:10px;font-weight:700;color:var(--ink);text-transform:uppercase}
.feature h3.hl{color:var(--brand)}
.feature p{position:absolute;top:146px;left:6px;width:172px;font-size:7.2px;line-height:10px;color:var(--muted)}
.feature svg{position:absolute;left:0;top:26px}

/* services */
.services{left:0;top:610px;width:672px;height:178px;background:var(--light)}
.section-title{width:672px;left:0;text-align:center;font-family:"Raleway",Arial,sans-serif;font-size:17.5px;color:#333}
.section-title span{color:var(--brand)}
.title-rule{width:170px;left:251px;height:1px;background:#bbb}
.title-badge{width:9px;height:9px;left:331px;background:var(--brand)}
.card{top:670px;width:165px;height:94px}
.card .caption{position:absolute;left:0;bottom:0;width:100%;height:19px;background:rgba(13,86,160,.85);color:#fff;font-size:10px;text-align:center;line-height:19px;font-family:"Raleway",Arial,sans-serif}
.card-overlay{background:#1a5fa0;color:#fff;text-align:center}
.card-overlay h4{font-size:10.5px;font-weight:700;margin-top:14px}
.card-overlay p{font-size:6.5px;line-height:9.5px;margin:6px 12px 0}
.card-overlay .more{font-size:6.5px;font-weight:700;margin-top:5px}

/* testimonial */
.avatar{left:70px;top:858px;width:80px;height:80px;border-radius:50%;border:3px solid #ccc;background:radial-gradient(circle at 50% 40%,#9aa7b4,#4a5868 70%,#2a3340)}
.quote{left:168px;top:855px;width:440px;font-size:7.2px;line-height:13.5px;font-style:italic;color:#666;text-align:center}
.quote-rule{left:168px;top:918px;width:440px;height:1px;background:#e3e3e3}
.author{left:222px;top:929px;font-size:7.5px;font-weight:600;color:var(--navy)}
.dots{left:524px;top:931px;display:flex;gap:3px}
.dots i{width:5px;height:5px;border-radius:50%;background:#ccc}
.dots i.on{background:var(--brand)}

/* footer */
.footer-col h5{font-family:"Raleway",Arial,sans-serif;font-size:10px;font-weight:600;color:#fff}
.footer-col ul{list-style:none;margin-top:12px}
.footer-col li{font-size:7px;color:#d5e6f5;line-height:21px}
.footer-col li::before{content:"▪";font-size:6px;margin-right:5px}
.contact-row{display:flex;gap:8px;font-size:7px;line-height:10px;color:#d5e6f5;margin-top:9px}
.contact-row svg{flex:none;margin-top:1px}
.field{left:306px;width:150px;height:19px;border:1px solid #8fb7dd;border-radius:2px;font-size:7px;color:#e1eef9;padding:5px 7px}
.submit{left:306px;top:1141px;width:58px;height:18px;background:linear-gradient(#fff,#dcdcdc);border-radius:2px;font-size:7.5px;color:#333;display:flex;align-items:center;justify-content:center}
.col-divider{top:1040px;width:1px;height:120px;background:rgba(255,255,255,.12)}
.social{top:1115px;width:17px;height:17px;border-radius:2px}
.copyright{left:0;top:1175px;width:672px;height:25px;background:var(--navy-deep);color:#d5e6f5;font-size:7px;display:flex;align-items:center;justify-content:center}
</style>
</head>
<body>

<header class="abs topbar"></header>
<div class="abs brand"><span class="brand-mark"></span>Beacon Advisory</div>

<div class="abs contact-chip" style="left:374px">
  <span class="dot"><svg width="8" height="10" viewBox="0 0 8 10"><rect x="1" y="0.5" width="6" height="9" rx="1" fill="none" stroke="#fff"/></svg></span>
  <div><div class="label">CALL US</div><div class="value">+1 (555) 318 2940</div></div>
</div>
<div class="abs contact-chip" style="left:475px">
  <span class="dot"><svg width="10" height="8" viewBox="0 0 10 8"><rect x="0.5" y="0.5" width="9" height="7" fill="none" stroke="#fff"/><path d="M0.5 0.5 L5 4.5 L9.5 0.5" fill="none" stroke="#fff"/></svg></span>
  <div><div class="label">EMAIL US</div><div class="value">info@beaconadvisoryinc.com</div></div>
</div>

<nav class="abs nav">
  <a class="active" style="width:62px">HOME</a>
  <a style="width:84px">ABOUT US</a>
  <a style="width:78px">SERVICES</a>
  <a style="width:84px">SOLUTIONS</a>
  <a style="width:86px">RESOURCES</a>
  <a style="width:71px">CAREER</a>
  <a style="width:90px;border-right:0">CONTACT US</a>
</nav>

<section>
  <div class="abs hero"></div>
  <div class="abs hero-visual" role="img" aria-label="Hand holding a tablet with a glowing globe and floating app windows"></div>
  <h2 class="abs hero-title heading">Delivers highest level of quality consultants and services for the lowest cost of ownership</h2>
  <div class="abs btn-more heading">READ MORE</div>
</section>

<section>
  <div class="abs welcome"></div>
  <div class="welcome"><h1 class="abs heading">Welcome To Beacon Advisoryinc</h1></div>
  <div class="abs welcome-rule"></div>
  <svg class="abs" style="left:330px;top:338px" width="12" height="6"><path d="M0 0 L6 5 L12 0Z" fill="#fff"/></svg>
  <div class="welcome"><p class="abs">Today's IT market is a dynamic, fast-paced industry, with ever-increasing demands. Meeting these demands for over 25 years, Beacon Advisory maintains a global presence, aggressively recruiting expertly qualified IT and Management Professionals from around the world and cultivating key partnerships with corporations to understand their business models end-to-end, with a goal of delivering exceptional client service and ensuring a consistent delivery....</p></div>
  <div class="abs plus">+</div>
</section>

<section>
  <div class="abs feature" style="left:57px">
    <svg width="184" height="100" viewBox="0 0 184 100">
      <g fill="none" stroke="#444" stroke-width="1">
        <polyline points="82,12 92,4 102,12"/><polyline points="82,80 92,88 102,80"/>
        <polyline points="56,38 50,46 56,54"/><polyline points="128,38 134,46 128,54"/>
      </g>
      <g fill="#222">
        <circle cx="83" cy="38" r="3"/><circle cx="101" cy="38" r="3"/>
        <rect x="79" y="42" width="8" height="7"/><rect x="97" y="42" width="8" height="7"/>
        <rect x="78" y="49" width="28" height="2"/>
        <rect x="80" y="51" width="2" height="7"/><rect x="102" y="51" width="2" height="7"/>
        <rect x="89" y="46" width="6" height="12"/>
      </g>
    </svg>
    <h3>Consulting</h3>
    <p>Beacon Advisory has certified professional consultants to work with you to help increase the business by providing IT services ...</p>
  </div>
  <div class="abs feature" style="left:252px">
    <svg width="184" height="100" viewBox="0 0 184 100">
      <g fill="none" stroke="#0a9fd8" stroke-width="1">
        <polyline points="82,4 92,12 102,4"/><polyline points="82,88 92,80 102,88"/>
        <polyline points="50,38 56,46 50,54"/><polyline points="134,38 128,46 134,54"/>
      </g>
      <circle cx="92" cy="46" r="9" fill="none" stroke="#0a9fd8" stroke-width="5" stroke-dasharray="3.2 2"/>
      <circle cx="92" cy="46" r="7.5" fill="#0a9fd8"/>
      <circle cx="92" cy="46" r="3" fill="#fff"/>
    </svg>
    <h3 class="hl">Staff Augmentation</h3>
    <p>For years Beacon Advisory as been offering our customers the ability to augment their existing staff..</p>
  </div>
  <div class="abs feature" style="left:435px">
    <svg width="184" height="100" viewBox="0 0 184 100">
      <g fill="none" stroke="#444" stroke-width="1">
        <polyline points="82,12 92,4 102,12"/><polyline points="82,80 92,88 102,80"/>
        <polyline points="56,38 50,46 56,54"/><polyline points="128,38 134,46 128,54"/>
      </g>
      <rect x="80" y="34" width="24" height="24" rx="3" fill="#2b2b2b"/>
    </svg>
    <h3>Offshore</h3>
    <p>Our Offshore development model has a unique distinction of providing efficient software solutions ...</p>
  </div>
</section>

<section>
  <div class="abs services"></div>
  <h2 class="abs section-title" style="top:618px;font-weight:400">Our <span>Services</span></h2>
  <div class="abs title-rule" style="top:646px"></div>
  <div class="abs title-badge" style="top:642px"></div>
  <svg class="abs" style="left:28px;top:700px" width="16" height="30"><polyline points="14,1 2,15 14,29" fill="none" stroke="#999"/></svg>
  <svg class="abs" style="left:626px;top:700px" width="16" height="30"><polyline points="2,1 14,15 2,29" fill="none" stroke="#999"/></svg>

  <div class="abs card" style="left:60px;background:linear-gradient(135deg,#0c1c2e,#3e6f9a 55%,#0f2438)" role="img" aria-label="Businessman touching a digital interface of technology icons">
    <div class="caption">Technology</div>
  </div>
  <div class="abs card card-overlay" style="left:253px">
    <h4>OFFSHORE</h4>
    <p>Our Offshore development model has a unique distinction of providing efficient software solutions with cost and quality advantage, using state-of-the-art</p>
    <div class="more">READ MORE »</div>
  </div>
  <div class="abs card" style="left:447px;background:linear-gradient(135deg,#2f87c6,#0f5596 60%,#0a3c70)" role="img" aria-label="Person pointing at floating application icons">
    <div class="caption">Application Developement</div>
  </div>
</section>

<section>
  <h2 class="abs section-title" style="top:806px;font-weight:400">Client <span>Testimonial</span></h2>
  <div class="abs title-rule" style="top:834px"></div>
  <div class="abs title-badge" style="top:830px"></div>
  <div class="abs avatar" role="img" aria-label="Portrait of the client giving the testimonial"></div>
  <svg class="abs" style="left:151px;top:856px" width="10" height="8"><path d="M0 8V4L3 0H5L3 4H5V8ZM5 8V4L8 0H10L8 4H10V8Z" fill="#bbb"/></svg>
  <p class="abs quote">Lorem ipsum dolor sit amet, consectetuer adipiscing elit, sed diam nonummy nibh euismod tincidunt utvm laoreetm dolore magna aliquam erat volutpat. Ut wisi enim ad minim veniam, quis nostrud exerci tation ullamcorper suscipit lobortis nisl utmv aliquip ex ea commodo consequat. Duis autem vel eum iriure dolor in hendrerit in vulputate velit esse molestie consequat, velm illu dolore eu feugiat nulla facilisis at vero eros et accumsan etsto duis facilisi.</p>
  <svg class="abs" style="left:496px;top:900px" width="10" height="8"><path d="M10 0V4L7 8H5L7 4H5V0ZM5 0V4L2 8H0L2 4H0V0Z" fill="#bbb"/></svg>
  <div class="abs quote-rule"></div>
  <svg class="abs" style="left:250px;top:918px" width="10" height="5"><path d="M0 0 L5 5 L10 0Z" fill="#ddd"/></svg>
  <div class="abs author">- Miss Clara Whitfield</div>
  <div class="abs dots"><i class="on"></i><i></i><i></i><i></i></div>
</section>

<footer>
  <svg class="abs" style="left:0;top:920px" width="672" height="255" viewBox="0 0 672 255">
    <path d="M0 83 C70 50 160 38 240 50 C300 60 330 90 390 88 C480 84 590 40 672 10 V255 H0Z" fill="#1560a6"/>
    <path d="M270 62 C330 88 390 94 450 82 C540 64 610 30 672 0 V12 C600 44 540 78 450 92 C380 102 320 90 270 62Z" fill="#12a9ea"/>
    <path d="M270 62 C330 88 390 94 450 82 C540 64 610 30 672 0" fill="none" stroke="#fff" stroke-width="1.5"/>
  </svg>

  <div class="abs footer-col" style="left:60px;top:1030px">
    <h5>Quick Links</h5>
    <ul><li>Home</li><li>About Us</li><li>Services</li><li>Resources</li><li>Contact Us</li></ul>
  </div>
  <div class="abs col-divider" style="left:150px"></div>

  <div class="abs footer-col" style="left:159px;top:1030px;width:130px">
    <h5>Contact Information</h5>
    <div class="contact-row" style="margin-top:10px"><svg width="7" height="10" viewBox="0 0 7 10"><path d="M3.5 0A3.5 3.5 0 0 0 0 3.5C0 6 3.5 10 3.5 10S7 6 7 3.5A3.5 3.5 0 0 0 3.5 0Z" fill="#fff"/><circle cx="3.5" cy="3.5" r="1.2" fill="#1560a6"/></svg><span>240 Harbor Lane<br>Suite 12<br>Fairview, NJ 07000</span></div>
    <div class="contact-row" style="margin-top:12px"><svg width="8" height="8" viewBox="0 0 8 8"><path d="M1 0H3L3.6 2L2.5 3A5 5 0 0 0 5 5.5L6 4.4L8 5V7L7 8C3 8 0 5 0 1Z" fill="#fff"/></svg><span>+1 (555) 318 2940</span></div>
    <div class="contact-row" style="margin-top:12px"><svg width="8" height="8" viewBox="0 0 8 8"><rect x="0" y="2.5" width="8" height="4" fill="#fff"/><rect x="2" y="0" width="4" height="2" fill="#fff"/><rect x="2" y="6" width="4" height="2" fill="#fff"/></svg><span>555.010.2288</span></div>
    <div class="contact-row" style="margin-top:12px"><svg width="8" height="6" viewBox="0 0 8 6"><rect width="8" height="6" fill="#fff"/><path d="M0 0L4 3.5L8 0" fill="none" stroke="#1560a6" stroke-width=".8"/></svg><span>info@samplemail.com</span></div>
  </div>
  <div class="abs col-divider" style="left:281px"></div>

  <div class="abs footer-col" style="left:306px;top:1030px"><h5>Quick Contact</h5></div>
  <div class="abs field" style="top:1052px">Name</div>
  <div class="abs field" style="top:1075px">Phone</div>
  <div class="abs field" style="top:1098px;height:34px">Message</div>
  <div class="abs submit">SUBMIT</div>
  <div class="abs col-divider" style="left:475px"></div>

  <div class="abs brand" style="left:500px;top:1068px;font-size:14px;color:#fff"><span class="brand-mark" style="width:18px;height:18px;background:#fff"></span>Beacon Advisory</div>
  <div class="abs social" style="left:504px;background:#1c3f8f"></div>
  <div class="abs social" style="left:528px;background:#3fb1e0"></div>
  <div class="abs social" style="left:552px;background:#1a8fd0"></div>
  <div class="abs social" style="left:578px;background:#f0a020"></div>

  <div class="abs copyright">Copyright © 2016 Beaconadvisoryinc. All Rights Reserved.</div>
</footer>

</body>
</html>
```